Kestrel Facilities Business Card Design

We would now like to design business cards with the new Kestrel Facilities logo

Target Market(s)

Professional

Industry/Entity Type

Professional services

Contact Information for Business Card

Employee name, title, phone number, email address, corporate office address and logo.

Font styles to use
Sans Serif

Colors
0054AA
0677BA
7BADD7
CADEEF
E8F1F8

Requirements
Must have
• My logo
Should not have
• any other pictures or images besides my logo

```html
<!DOCTYPE html>
<html lang="en">
<head>
<meta charset="utf-8">
<title>Kestrel Facilities Business Card</title>
<link rel="stylesheet" href="https://fonts.googleapis.com/css2?family=Roboto+Condensed:wght@400;700&family=Roboto:wght@400&display=swap">
<style>
  :root {
    --brand-blue: #1a74de;
    --paper: #f7f7f5;
    --ink: #3a3a3a;
    --muted: #5a5a5a;
    --stage: #d9dce1;
  }
  * { box-sizing: border-box; margin: 0; padding: 0; }
  html, body { width: 1200px; height: 874px; overflow: hidden; }
  body {
    background: var(--stage);
    position: relative;
    font-family: "Roboto", Arial, sans-serif;
  }
  .card {
    position: absolute;
    left: 290px;
    width: 620px;
    height: 354px;
    box-shadow: 0 6px 18px rgba(0,0,0,0.18);
  }
  .card-front { top: 63px; background: var(--brand-blue); }
  .card-back { top: 457px; background: var(--paper); }
  .frame {
    position: absolute;
    inset: 16px;
    border: 5px solid;
  }
  .card-front .frame { border-color: #ffffff; }
  .card-back .frame { border-color: var(--brand-blue); }

  .brand {
    position: absolute;
    left: 0; right: 0; top: 0; bottom: 0;
    display: flex;
    align-items: center;
    justify-content: center;
    gap: 16px;
  }
  .brand-mark {
    width: 46px; height: 46px;
    background: #ffffff;
  }
  .brand-name {
    font-family: "Roboto Condensed", Arial, sans-serif;
    font-weight: 700;
    font-size: 44px;
    letter-spacing: 1px;
    text-transform: uppercase;
    color: #ffffff;
  }

  .identity {
    position: absolute;
    right: 370px;
    top: 118px;
    text-align: right;
  }
  .person-name {
    font-family: "Roboto Condensed", Arial, sans-serif;
    font-weight: 700;
    font-size: 36px;
    color: var(--brand-blue);
    text-transform: uppercase;
    line-height: 1;
  }
  .person-title {
    font-size: 17px;
    color: var(--muted);
    margin-top: 4px;
  }
  .divider {
    position: absolute;
    left: 270px;
    top: 125px;
    width: 2px;
    height: 62px;
    background: var(--brand-blue);
  }
  .contacts {
    position: absolute;
    left: 290px;
    top: 122px;
    list-style: none;
  }
  .contacts li {
    display: flex;
    align-items: center;
    gap: 10px;
    font-size: 17px;
    color: var(--ink);
    line-height: 23px;
  }
  .contacts svg { width: 13px; height: 13px; fill: var(--brand-blue); flex: none; }
  .address {
    position: absolute;
    left: 64px;
    top: 250px;
    font-size: 17px;
    color: var(--ink);
  }
</style>
</head>
<body>
  <section class="card card-front">
    <div class="frame"></div>
    <div class="brand">
      <span class="brand-mark"></span>
      <span class="brand-name">Kestrel Facilities</span>
    </div>
  </section>

  <section class="card card-back">
    <div class="frame"></div>
    <div class="identity">
      <div class="person-name">Daniel Reeve</div>
      <div class="person-title">President</div>
    </div>
    <div class="divider"></div>
    <ul class="contacts">
      <li>
        <svg viewBox="0 0 24 24" aria-hidden="true"><path d="M6.6 10.8a15.1 15.1 0 0 0 6.6 6.6l2.2-2.2c.3-.3.7-.4 1-.2 1.1.4 2.3.6 3.6.6.6 0 1 .4 1 1V20c0 .6-.4 1-1 1A17 17 0 0 1 3 4c0-.6.4-1 1-1h3.5c.6 0 1 .4 1 1 0 1.3.2 2.5.6 3.6.1.3 0 .7-.2 1z"/></svg>
        555-014-2287
      </li>
      <li>
        <svg viewBox="0 0 24 24" aria-hidden="true"><path d="M2 5h20v14H2z M2 5l10 8 10-8" fill="none" stroke="#1a74de" stroke-width="2.4"/></svg>
        info@kestrelfacilities.com
      </li>
      <li>
        <svg viewBox="0 0 24 24" aria-hidden="true"><circle cx="12" cy="12" r="10"/><path d="M2 12h20M12 2c3 3 3 17 0 20M12 2c-3 3-3 17 0 20" fill="none" stroke="#f7f7f5" stroke-width="1.4"/></svg>
        kestrelfacilities.com
      </li>
    </ul>
    <p class="address">2214 Birchwood Road, Fairbanks, Alaska 99701</p>
  </section>
</body>
</html>
```